Property Finance Company - Orbin Funding Limited

Background: Orbin Funding Group Limited is a private property finance company. Orbin Funding Group has capital to directly fund first mortgage, mezzanine and preferred equity financing. We also acquire performing, sub-performing and distressed debt.

Orbin Fundings management philosophy emphasises expertise, innovation, wisdom, honesty and competitiveness. Orbin Funding are not finance brokers - we provide debt funding to the commercial property and residential development sectors. Our process is built from experience and cumutavely Orbin Fundings Directors have in excess of 60 years wisdom.

The aim of the website will be to increase brand awareness, provide clients with comfort around our level of skill and background on who we are, generate more sales, and provide examples of projects that we have funded.

The website is a new product launch, and we need to use our Orbin Funding logo that has just been designed. We like a dark background, and either black/silver/grey/ jade green, or black/gold/jade green colours.

Our unique advantages are that we have fast turnaround times, we can solve clients funding problems and we know what we are doing. Our target audience will be viewing the website on both desktop and mobile devices.

We would like to have the following pages:

Home
About
Team
Services
Project Experience
Contact

Competitors Website: http://www.tarvolo.example/

We would also like to have the option of video footage in our website, as you can see in our competitors website.

Overall we want a really slick, elegant but modern website that is better than www.tarvolo.example

Target Market(s)

Finance borrowers, property developers, accountants, lawyers, businesspeople, high net worth people

Industry/Entity Type

Finance

Requirements
Must have
• Please see project description
Nice to have
Should not have

```html
<!DOCTYPE html>
<html lang="en">
<head>
<meta charset="utf-8">
<title>Orbin Funding</title>
<link href="https://fonts.googleapis.com/css2?family=Montserrat:wght@400;500;600&family=Poppins:wght@400;500&display=swap" rel="stylesheet">
<style>
:root{
  --black:#050505;
  --white:#ffffff;
  --gold-1:#b98f1e;
  --gold-2:#e6c765;
  --gold-3:#f3dc8e;
  --panel:rgba(255,250,235,0.55);
  --card:rgba(255,252,242,0.82);
  --ink:#2a2720;
  --muted:#6f6a5c;
  --teal-1:#3d7180;
  --teal-2:#173845;
  --green:#058245;
}
*{margin:0;padding:0;box-sizing:border-box}
html,body{width:769px;height:1200px;overflow:hidden;background:var(--black)}
body{position:relative;font-family:'Montserrat',sans-serif;color:var(--white)}
.abs{position:absolute}
.hero{left:0;top:0;width:769px;height:386px;
  background:radial-gradient(ellipse at 62% 45%,#4a3f6e 0%,#241d36 30%,#0d0c14 65%,#030303 100%)}
.brand{left:56px;top:20px;display:flex;align-items:center;gap:6px;font-size:11px;font-weight:500;letter-spacing:.5px}
.brand .dot{width:10px;height:10px;border-radius:50%;background:var(--white)}
.nav{top:44px;font-size:7.5px;font-weight:500;letter-spacing:.2px}
.welcome{left:53px;top:152px;font-size:16px;letter-spacing:.5px}
.title{left:52px;top:172px;font-size:34px;font-weight:500;letter-spacing:.3px}
.tagline{left:54px;top:217px;font-family:'Poppins',sans-serif;font-size:13px}
.watch{left:54px;top:247px;width:106px;height:29px;border-radius:2px;
  background:linear-gradient(#4e8594,var(--teal-2));display:flex;align-items:center;justify-content:center;gap:7px;font-size:10px;font-weight:500}
.gold{left:0;top:386px;width:769px;height:534px;
  background:linear-gradient(100deg,var(--gold-1) 0%,var(--gold-2) 25%,var(--gold-3) 45%,var(--gold-2) 65%,var(--gold-1) 100%)}
.about-box{left:54px;top:424px;width:660px;height:216px;background:var(--panel)}
.about-label{left:78px;top:505px;color:var(--ink);font-size:17px}
.about-name{left:76px;top:524px;color:var(--ink);font-size:24px}
.about-text{left:259px;top:445px;width:440px;color:#3a362c;font-size:10.6px;line-height:18.8px}
.about-text p+p{margin-top:18.8px}
.services-h{left:54px;top:676px;color:#111;font-size:24px}
.card{top:720px;width:204px;height:146px;background:var(--card);padding:19px 8px 0 9px}
.card h3{color:#222;font-size:11px;font-weight:600;margin-bottom:6px}
.card p{color:var(--muted);font-size:8.4px;line-height:14.8px;padding-left:1px}
.card a{display:block;margin-top:15px;color:var(--muted);font-size:8.4px;text-decoration:none;padding-left:1px}
.footer-h{top:940px;font-size:11px;font-weight:500}
.ftext{font-size:9px;line-height:18px}
.input{left:335px;width:187px;height:27px;background:var(--white);color:#555;font-size:7px;padding:10px 0 0 9px}
.subscribe{left:335px;top:1073px;width:106px;height:27px;border-radius:2px;background:linear-gradient(#4e8594,var(--teal-2));font-size:8px;display:flex;align-items:center;justify-content:center}
.links{left:623px;top:972px;font-size:9px;line-height:22.4px;list-style:none}
.links li::before{content:"›";margin-right:8px}
.bar{left:0;top:1139px;width:769px;height:61px;background:var(--green)}
.copy{left:56px;top:1166px;font-size:7.5px}
.follow{left:589px;top:1166px;font-size:7.5px}
.social{top:1163px;width:18px;height:18px;border-radius:50%}
</style>
</head>
<body>
<div class="abs hero" role="img" aria-label="Night city skyline with lit skyscrapers"></div>
<div class="abs brand"><span class="dot"></span>ORBIN FUNDING</div>
<div class="abs nav" style="left:378px">HOME</div>
<div class="abs nav" style="left:424px">ABOUT</div>
<div class="abs nav" style="left:472px">TEAM</div>
<div class="abs nav" style="left:514px">SERVICES</div>
<div class="abs nav" style="left:573px">PROJECT EXPERIENCE</div>
<div class="abs nav" style="left:678px">CONTACT</div>
<div class="abs welcome">WELCOME TO</div>
<div class="abs title">ORBIN FUNDING</div>
<div class="abs tagline">We are private property finance company.</div>
<div class="abs watch"><svg width="10" height="10" viewBox="0 0 10 10"><circle cx="5" cy="5" r="5" fill="#fff"/><path d="M4 3l3 2-3 2z" fill="#173845"/></svg>WATCH NOW</div>

<div class="abs gold" role="img" aria-label="Brushed gold texture"></div>
<div class="abs about-box"></div>
<div class="abs about-label">About</div>
<div class="abs about-name">Orbin Funding</div>
<div class="abs about-text">
<p>Orbin Funding Group Limited is a private property finance company. Orbin Funding Group has capital to directly fund first mortgage, mezzanine and preferred equity financing. We also acquire performing, sub-performing and distressed debt.</p>
<p>Orbin Fundings management philosophy emphasises expertise, innovation, wisdom, honesty and competitiveness. Orbin Funding are not finance brokers - we provide debt funding to the commercial property and residential development sectors. Our process is built from experience and cumutavely Orbin Fundings Directors have in excess of 60 years wisdom.</p>
</div>
<div class="abs services-h">Services</div>
<div class="abs card" style="left:54px"><h3>DEBT FUNDING</h3><p>Lorem Ipsum is simply dummy text of the printing and typesetting industry. Lorem Ipsum has been the industry's standard dummy text ever since the 1500s,</p><a>Read More &gt;</a></div>
<div class="abs card" style="left:283px"><h3>EQUITY FINANCING</h3><p>Lorem Ipsum is simply dummy text of the printing and typesetting industry. Lorem Ipsum has been the industry's standard dummy text ever since the 1500s,</p><a>Read More &gt;</a></div>
<div class="abs card" style="left:510px"><h3>DISTRESSED DEBT</h3><p>Lorem Ipsum is simply dummy text of the printing and typesetting industry. Lorem Ipsum has been the industry's standard dummy text ever since the 1500s,</p><a>Read More &gt;</a></div>

<div class="abs footer-h" style="left:54px">CONTACT US</div>
<svg class="abs" style="left:54px;top:975px" width="11" height="14" viewBox="0 0 11 14"><path d="M5.5 13S1 8 1 5a4.5 4.5 0 0 1 9 0c0 3-4.5 8-4.5 8z" fill="none" stroke="#fff" stroke-width="1"/><circle cx="5.5" cy="5" r="1.6" fill="none" stroke="#fff"/></svg>
<div class="abs ftext" style="left:77px;top:968px">Orbin Funding<br>218 Harbour Crest Rd, Westvale, CA 90000</div>
<svg class="abs" style="left:54px;top:1023px" width="12" height="12" viewBox="0 0 12 12"><path d="M2 1l2 0 1 3-1.5 1a6 6 0 0 0 3.5 3.5L8 7l3 1v2a1 1 0 0 1-1 1A9 9 0 0 1 1 2a1 1 0 0 1 1-1z" fill="none" stroke="#fff" stroke-width=".9"/></svg>
<div class="abs ftext" style="left:77px;top:1021px">Phone : 0100 555 018</div>
<svg class="abs" style="left:54px;top:1062px" width="13" height="10" viewBox="0 0 13 10"><rect x=".5" y=".5" width="12" height="9" fill="none" stroke="#fff"/><path d="M.5 .5l6 5 6-5" fill="none" stroke="#fff"/></svg>
<div class="abs ftext" style="left:77px;top:1057px">Email: info@orbinfunding.example</div>

<div class="abs footer-h" style="left:336px">JOIN THE MAILING LIST</div>
<div class="abs" style="left:337px;top:966px;font-size:8px;line-height:13px">Stay informed about the latest and<br>greatest here at Orbin Funding!</div>
<div class="abs input" style="top:1005px">Name</div>
<div class="abs input" style="top:1038px">Email Address</div>
<div class="abs subscribe">SUBSCRIBE</div>

<div class="abs footer-h" style="left:623px">QUICK LINKS</div>
<ul class="abs links"><li>Home</li><li>About</li><li>Team</li><li>Services</li><li>Project Experience</li><li>Contact</li></ul>

<div class="abs bar"></div>
<div class="abs copy">Copyright © 2017. Orbin Funding. All rights reserved.</div>
<div class="abs follow">Follow us:</div>
<div class="abs social" style="left:639px;background:#3b5a98"></div>
<div class="abs social" style="left:665px;background:#4aa1de"></div>
<div class="abs social" style="left:692px;background:#d8262b"></div>
</body>
</html>
```